Business card

We need a business card design for our company based in Auckland , New Zealand called 'Ridge + Studio Ltd'. We provide architectural services. We would like to see designs that use the max. three colours (such as white, black, grey) The final design should communicate financial safety and growth."
Also I will provide our company logo. I would like to the logo to be embeded onto our business card.

Target Market(s)

new residential house, alteration & addition & light commericila design & drafting service

Industry/Entity Type

Architecture

Contact Information for Business Card

Company name: ridge + studio Ltd.
Name: Mark Delford
Job title: architectural designer & Design LBP
email address: mark@kowhaidesign.co.nz
mobile number: 02 5163 2290
web site: www.kowhaidesign.co.nz

Requirements
Must have
• My project must have..
• - embeded logo (attached company logo)
• I don't have a bigger version for our company logo, but I have one old one, so you can remove the word from it)
• - insert the attached small BKTW logo & LBP logo
• - creative, simple and clear business card.
• - Max. three colours
Nice to have
• - Here are the samples I would like to share with you: http://www.plimvora.com/blog/minimalistic-business-card-designs/
• I would like to have my business card like one of the creation.
Should not have
• TBA

```html
<!DOCTYPE html>
<html lang="en">
<head>
<meta charset="utf-8">
<title>Kowhai Design Studio — Business Card</title>
<link rel="stylesheet" href="https://fonts.googleapis.com/css2?family=Open+Sans:wght@400;600&family=Roboto:wght@400;500&display=swap">
<style>
  :root {
    --paper: #ffffff;
    --ink: #111111;
    --stage: #e9e9e9;
    --badge: #3a3a3a;
    --card-shadow: 0 6px 22px rgba(0,0,0,0.18);
  }
  * { box-sizing: border-box; margin: 0; padding: 0; }
  html, body { width: 1200px; height: 900px; overflow: hidden; }
  body { background: var(--stage); position: relative; color: var(--ink); }

  .card {
    position: absolute;
    background: var(--paper);
    box-shadow: var(--card-shadow);
    overflow: hidden;
  }
  .card--front { left: 238px; top: 62px; width: 555px; height: 343px; }
  .card--back  { left: 457px; top: 518px; width: 560px; height: 344px; }

  .company-name {
    font-family: "Roboto", sans-serif;
    font-weight: 400;
    font-size: 24px;
    line-height: 30px;
    letter-spacing: 0.1px;
    color: var(--ink);
    white-space: nowrap;
  }
  .card--front .company-name { position: absolute; left: 34px; top: 50px; }

  .holder { position: absolute; left: 34px; top: 164px; font-family: "Open Sans", sans-serif; }
  .holder__name { font-weight: 600; font-size: 17px; line-height: 22px; }
  .holder__role { font-weight: 400; font-size: 14px; line-height: 19px; }

  .contacts { position: absolute; left: 34px; top: 254px; list-style: none; font-family: "Open Sans", sans-serif; font-size: 14px; }
  .contacts li { display: flex; align-items: center; height: 20px; white-space: nowrap; }
  .contacts svg { width: 11px; height: 11px; margin-right: 9px; fill: var(--ink); flex: none; }

  .brand-disc { position: absolute; left: 312px; top: -52px; width: 490px; height: 490px; border-radius: 50%; background: var(--ink); }

  .brand-lockup { position: absolute; left: 0; top: 22px; width: 100%; display: flex; flex-direction: column; align-items: center; }
  .brand-lockup__mark { width: 130px; height: 130px; border-radius: 50%; border: 10px solid var(--ink); margin-bottom: 10px; }

  .memberships { position: absolute; left: 163px; top: 225px; display: flex; align-items: center; gap: 22px; }
  .memberships__badge-rect { width: 115px; height: 84px; background: var(--badge); }
  .memberships__badge-round { width: 96px; height: 96px; border-radius: 50%; background: var(--badge); }
</style>
</head>
<body>

  <section class="card card--front" aria-label="Business card front">
    <h1 class="company-name">Kowhai Design Studio</h1>

    <div class="holder">
      <p class="holder__name">Mark Delford</p>
      <p class="holder__role">Architectural designer &amp; Design LBP</p>
    </div>

    <ul class="contacts">
      <li>
        <svg viewBox="0 0 12 12" aria-hidden="true"><path d="M2.4 0.6 L4.3 2.8 L3.3 4.3 C4 5.8 6 7.8 7.6 8.6 L9.1 7.6 L11.4 9.5 L10.2 11.3 C5.4 11 0.9 6.5 0.6 1.8 Z"/></svg>
        02 5163 2290
      </li>
      <li>
        <svg viewBox="0 0 12 12" aria-hidden="true"><path d="M0.5 2.5 H11.5 V10 H0.5 Z M1.2 3 L6 6.6 L10.8 3 Z" fill-rule="evenodd"/></svg>
        mark@kowhaidesign.co.nz
      </li>
      <li>
        <svg viewBox="0 0 12 12" aria-hidden="true"><circle cx="6" cy="6" r="5.5"/><path d="M3 4 Q5 3 6 5 Q5 7 7 8 L6 10 Q3 9 3 6 Z" fill="#fff"/></svg>
        www.kowhaidesign.co.nz
      </li>
    </ul>

    <div class="brand-disc" aria-hidden="true"></div>
  </section>

  <section class="card card--back" aria-label="Business card back">
    <div class="brand-lockup">
      <div class="brand-lockup__mark" aria-hidden="true"></div>
      <p class="company-name">Kowhai Design Studio</p>
    </div>

    <div class="memberships">
      <div class="memberships__badge-rect" role="img" aria-label="Professional membership badge"></div>
      <div class="memberships__badge-round" role="img" aria-label="Licensed building practitioner badge"></div>
    </div>
  </section>

</body>
</html>
```